Landscaping flier 2024

Create a 1 page flier for landscaping services
1. Must be completed in Adobe Photoshop
2. Size 8.5" x 11" (portrait layout)
3. Include logo
4. Text to include:
2024 Gravesite Landscaping Packages
info@hollowbrookmemorial.org
(201) 555-0148
hollowbrookmemorial.org
5. Use chart text for the content. DO NOT COPY THE CHART DESIGN/FORMAT. Use the chart for the text you need only.
6. Use "Pricing cards as format for laying out the chart". Open to other ideas as well.
**Use the example of chart design (handwritten) to base your design off of.
7. Photos
-include before and after care photos

```html
<!DOCTYPE html>
<html lang="en">
<head>
<meta charset="utf-8">
<title>2024 Gravesite Landscaping Packages</title>
<link href="https://fonts.googleapis.com/css2?family=Libre+Baskerville:wght@400;700&family=Montserrat:wght@400;500;600;700;800&display=swap" rel="stylesheet">
<style>
:root{
  --page:#ececec;
  --paper:#ffffff;
  --maroon:#8b1e3f;
  --maroon-dark:#6e1430;
  --navy:#26344a;
  --blue:#2a8ac4;
  --blue-tint:#e9f2f9;
  --green:#7cc242;
  --green-text:#4f9a22;
  --green-tint:#eff6e4;
  --pink-tint:#f9e6ec;
  --gold:#d8b45a;
  --ink:#3b3b3b;
  --muted:#6b6b6b;
  --bullet-red:#d8413f;
  --bullet-green:#6cb43a;
}
*{box-sizing:border-box;margin:0;padding:0}
html,body{width:1200px;height:2415px;overflow:hidden;background:var(--page)}
body{font-family:"Montserrat",sans-serif;color:var(--ink);position:relative}

.flier{position:absolute;left:50px;top:495px;width:1100px;height:1424px;background:var(--paper);overflow:hidden;box-shadow:0 4px 18px rgba(0,0,0,.12)}

.title{position:absolute;top:38px;left:0;width:100%;text-align:center;font-family:"Libre Baskerville",serif;font-weight:700;color:var(--maroon);text-transform:uppercase;z-index:3}
.title .line1{font-size:42px;letter-spacing:1px;display:block}
.title .line2{font-size:44px;letter-spacing:1px;display:block;margin-top:16px}

.hero{position:absolute;left:0;top:150px;width:100%;height:320px;background:linear-gradient(180deg,#ffffff 0%,#dfe8cf 18%,#c9c77a 35%,#6f8a55 62%,#3f5a33 100%)}
.hero-band{position:absolute;left:0;top:420px;width:100%;height:70px}

.card{position:absolute;top:460px;height:618px;border-bottom:4px solid}
.card .head{height:112px;color:#fff;text-align:center;padding-top:26px;clip-path:polygon(0 0,100% 0,100% 82%,50% 100%,0 82%)}
.card .head h2{font-size:23px;font-weight:700;letter-spacing:.3px;line-height:1.05;text-transform:uppercase}
.card .head p{font-size:9.5px;text-transform:uppercase;line-height:1.35;margin-top:6px;opacity:.92}
.seasonal{left:48px;width:312px;background:var(--blue-tint);border-color:var(--blue)}
.seasonal .head{background:var(--blue)}
.basic{left:372px;width:326px;background:var(--green-tint);border-color:var(--green);top:450px;height:628px}
.basic .head{background:var(--green)}
.perpetual{left:708px;width:344px;background:var(--pink-tint);border-color:var(--maroon);top:425px;height:653px}
.perpetual .head{background:var(--maroon);height:132px;padding-top:42px}

.ribbon{position:absolute;left:-8px;top:14px;background:var(--gold);color:#fff;font-size:8px;font-weight:700;padding:3px 16px;transform:rotate(-35deg);text-transform:uppercase}

.terms{display:flex;align-items:center;gap:16px;padding:22px 20px 0}
.year-dots{display:flex;gap:4px}
.year-dot{width:44px;height:70px;border-radius:22px;background:var(--blue);color:#fff;text-align:center;padding-top:6px}
.year-dot b{display:block;font-size:18px;line-height:1}
.year-dot small{display:block;font-size:6px;text-transform:uppercase}
.year-dot em{display:block;font-style:normal;font-size:10px;font-weight:700;margin-top:8px}
.terms .note{font-size:10px;line-height:1.35;color:var(--muted)}

.price{display:flex;align-items:flex-end;justify-content:center;gap:12px;padding-top:30px}
.price .label{font-size:10px;text-transform:uppercase;line-height:1.2;padding-bottom:8px}
.price .amount{font-size:46px;font-weight:600;line-height:1}
.price .amount sup{font-size:20px;vertical-align:top}
.basic .amount{color:var(--green-text)}
.perpetual .amount{color:var(--maroon)}
.discount{text-align:center;font-size:10px;color:var(--muted);margin-top:16px}

.weeding{display:flex;gap:14px;padding:24px 22px 0}
.weeding h3{flex:0 0 84px;font-size:9.5px;font-weight:700;text-transform:uppercase;line-height:1.2}
.weeding p{flex:1;font-size:9.5px;line-height:1.35;color:var(--muted)}
.basic .weeding h3{color:var(--green-text)}
.basic .weeding p{color:var(--green-text)}
.perpetual .weeding h3{color:var(--maroon)}
.seasonal .weeding h3{color:var(--navy)}

.features{list-style:none;padding:30px 22px 0 30px}
.features li{display:flex;align-items:flex-start;gap:10px;font-size:13.5px;line-height:1.3;margin-bottom:13px}
.features svg{flex:none;margin-top:2px}
.seasonal .features li{color:var(--navy)}
.basic .features li{color:var(--green-text)}
.perpetual .features li{color:var(--maroon)}

.brand{position:absolute;left:60px;top:1182px;width:520px;display:flex;align-items:center;gap:14px}
.brand-mark{flex:none;width:56px;height:56px;border-radius:50%;background:#d9d9d9}
.brand-name{font-family:"Libre Baskerville",serif;font-size:24px;color:var(--maroon);text-transform:uppercase;letter-spacing:.3px;white-space:nowrap}

.contact{position:absolute;left:110px;top:1275px;list-style:none}
.contact li{display:flex;align-items:center;gap:14px;margin-bottom:16px;font-size:17px;color:var(--navy)}
.contact li.phone{font-family:"Libre Baskerville",serif;font-weight:700;font-size:20px}

.proof{position:absolute;top:1178px;width:200px;height:222px}
.proof .tag{position:absolute;left:14px;top:0;background:var(--maroon);color:#fff;font-size:13px;font-style:italic;padding:4px 18px;z-index:2}
.proof .shot{position:absolute;inset:10px 0 0 0;background:linear-gradient(180deg,#b7c3b0 0%,#7e9a66 40%,#4f8a34 100%)}
.proof.before{left:610px}
.proof.after{left:840px}
</style>
</head>
<body>
<main class="flier">
  <h1 class="title"><span class="line1">2024 Gravesite</span><span class="line2">Landscaping Packages</span></h1>

  <div class="hero" role="img" aria-label="Photo of a cemetery lawn with headstones, autumn trees and a historic house"></div>
  <svg class="hero-band" viewBox="0 0 1100 70" preserveAspectRatio="none" aria-hidden="true">
    <polygon points="0,14 160,40 0,60" fill="var(--maroon)"/>
    <polygon points="1060,28 1100,20 1100,50" fill="var(--navy)"/>
  </svg>

  <section class="card seasonal">
    <div class="head"><h2>Seasonal Care</h2><p>Seasonal landscaping<br>grave care</p></div>
    <div class="terms">
      <div class="year-dots">
        <div class="year-dot"><b>1</b><small>year</small><em>$132</em></div>
        <div class="year-dot"><b>3</b><small>years</small><em>$396</em></div>
        <div class="year-dot"><b>2</b><small>years</small><em>$264</em></div>
      </div>
      <p class="note">Multi-year<br>payment locks<br>in current rates</p>
    </div>
    <div class="weeding"><h3>Weeding &amp; trimming on your gravesite</h3><p>Approximately Every 2 Weeks During The Growing Season Mid-April Through Mid-October</p></div>
    <ul class="features">
      <li><svg width="14" height="14" viewBox="0 0 14 14"><circle cx="7" cy="7" r="7" fill="var(--bullet-red)"/><path d="M4 7l2 2 4-4" stroke="#fff" stroke-width="1.6" fill="none"/></svg>Payment Ensures<br>Grave Care Forever</li>
      <li><svg width="14" height="14" viewBox="0 0 14 14"><circle cx="7" cy="7" r="7" fill="var(--bullet-red)"/><path d="M4 7l2 2 4-4" stroke="#fff" stroke-width="1.6" fill="none"/></svg>Monument Leveling</li>
      <li><svg width="14" height="14" viewBox="0 0 14 14"><circle cx="7" cy="7" r="7" fill="var(--bullet-red)"/><path d="M4 7l2 2 4-4" stroke="#fff" stroke-width="1.6" fill="none"/></svg>Monument Cleaning</li>
      <li><svg width="14" height="14" viewBox="0 0 14 14"><circle cx="7" cy="7" r="7" fill="var(--bullet-red)"/><path d="M4 7l2 2 4-4" stroke="#fff" stroke-width="1.6" fill="none"/></svg>Full Bed Of Boxwood Shrubs</li>
      <li><svg width="14" height="14" viewBox="0 0 14 14"><circle cx="7" cy="7" r="7" fill="var(--bullet-red)"/><path d="M4 7l2 2 4-4" stroke="#fff" stroke-width="1.6" fill="none"/></svg>Replacement Of Shrubs</li>
      <li><svg width="14" height="14" viewBox="0 0 14 14"><circle cx="7" cy="7" r="7" fill="var(--bullet-red)"/><path d="M4 7l2 2 4-4" stroke="#fff" stroke-width="1.6" fill="none"/></svg>Trust Certificate</li>
    </ul>
  </section>

  <section class="card basic">
    <div class="head"><h2>Basic Care<br>Endowment</h2><p>Landscaping care forever<br>for graves with no plantings</p></div>
    <div class="price"><span class="label">12 monthly<br>payments of</span><span class="amount"><sup>$</sup>287</span></div>
    <p class="discount">Call for single payment discount</p>
    <div class="weeding"><h3>Weeding &amp; trimming on your gravesite</h3><p>2 times per year:<br>mid-May &amp; mid-September</p></div>
    <ul class="features">
      <li><svg width="14" height="14" viewBox="0 0 14 14"><circle cx="7" cy="7" r="7" fill="var(--bullet-green)"/><path d="M4 7l2 2 4-4" stroke="#fff" stroke-width="1.6" fill="none"/></svg>Payment Ensures<br>Grave Care Forever</li>
      <li><svg width="14" height="14" viewBox="0 0 14 14"><circle cx="7" cy="7" r="7" fill="var(--bullet-green)"/><path d="M4 7l2 2 4-4" stroke="#fff" stroke-width="1.6" fill="none"/></svg>Monument Leveling</li>
      <li><svg width="14" height="14" viewBox="0 0 14 14"><circle cx="7" cy="7" r="7" fill="var(--bullet-green)"/><path d="M4 7l2 2 4-4" stroke="#fff" stroke-width="1.6" fill="none"/></svg>Monument Cleaning</li>
      <li><svg width="14" height="14" viewBox="0 0 14 14"><circle cx="7" cy="7" r="7" fill="var(--bullet-red)"/><path d="M4.5 4.5l5 5M9.5 4.5l-5 5" stroke="#fff" stroke-width="1.6"/></svg>Full Bed Of Boxwood Shrubs</li>
      <li><svg width="14" height="14" viewBox="0 0 14 14"><circle cx="7" cy="7" r="7" fill="var(--bullet-red)"/><path d="M4.5 4.5l5 5M9.5 4.5l-5 5" stroke="#fff" stroke-width="1.6"/></svg>Replacement Of Shrubs</li>
      <li><svg width="14" height="14" viewBox="0 0 14 14"><circle cx="7" cy="7" r="7" fill="var(--bullet-red)"/><path d="M4.5 4.5l5 5M9.5 4.5l-5 5" stroke="#fff" stroke-width="1.6"/></svg>Trust Certificate</li>
    </ul>
  </section>

  <section class="card perpetual">
    <div class="head"><span class="ribbon">Most popular</span><h2>Perpetual Care<br>Endowment</h2><p>Landscaping care forever<br>for graves with plantings</p></div>
    <div class="price"><span class="label">12 monthly<br>payments of</span><span class="amount"><sup>$</sup>351</span></div>
    <p class="discount">Call for single payment discount</p>
    <div class="weeding"><h3>Weeding &amp; trimming on your gravesite</h3><p>Approximately every 2 weeks during the growing season mid-April through mid-October</p></div>
    <ul class="features">
      <li><svg width="14" height="14" viewBox="0 0 14 14"><circle cx="7" cy="7" r="7" fill="var(--bullet-green)"/><path d="M4 7l2 2 4-4" stroke="#fff" stroke-width="1.6" fill="none"/></svg>Payment Ensures<br>Grave Care Forever</li>
      <li><svg width="14" height="14" viewBox="0 0 14 14"><circle cx="7" cy="7" r="7" fill="var(--bullet-green)"/><path d="M4 7l2 2 4-4" stroke="#fff" stroke-width="1.6" fill="none"/></svg>Monument Leveling</li>
      <li><svg width="14" height="14" viewBox="0 0 14 14"><circle cx="7" cy="7" r="7" fill="var(--bullet-green)"/><path d="M4 7l2 2 4-4" stroke="#fff" stroke-width="1.6" fill="none"/></svg>Monument Cleaning</li>
      <li><svg width="14" height="14" viewBox="0 0 14 14"><circle cx="7" cy="7" r="7" fill="var(--bullet-green)"/><path d="M4 7l2 2 4-4" stroke="#fff" stroke-width="1.6" fill="none"/></svg>Full Bed Of Boxwood Shrubs</li>
      <li><svg width="14" height="14" viewBox="0 0 14 14"><circle cx="7" cy="7" r="7" fill="var(--bullet-green)"/><path d="M4 7l2 2 4-4" stroke="#fff" stroke-width="1.6" fill="none"/></svg>Replacement Of Shrubs</li>
      <li><svg width="14" height="14" viewBox="0 0 14 14"><circle cx="7" cy="7" r="7" fill="var(--bullet-green)"/><path d="M4 7l2 2 4-4" stroke="#fff" stroke-width="1.6" fill="none"/></svg>Trust Certificate</li>
    </ul>
  </section>

  <div class="brand"><span class="brand-mark"></span><span class="brand-name">Hollowbrook Memorial</span></div>

  <ul class="contact">
    <li class="phone"><svg width="18" height="18" viewBox="0 0 24 24"><path d="M6.6 10.8a15 15 0 006.6 6.6l2.2-2.2c.3-.3.7-.4 1-.2 1.1.4 2.3.6 3.6.6.6 0 1 .4 1 1V20c0 .6-.4 1-1 1A17 17 0 013 4c0-.6.4-1 1-1h3.5c.6 0 1 .4 1 1 0 1.3.2 2.5.6 3.6.1.3 0 .7-.2 1z" fill="var(--maroon)"/></svg>(201) 555-0148</li>
    <li><svg width="18" height="18" viewBox="0 0 24 24"><rect x="3" y="5" width="18" height="14" rx="1.5" fill="none" stroke="var(--maroon)" stroke-width="2"/><path d="M3 6l9 7 9-7" fill="none" stroke="var(--maroon)" stroke-width="2"/></svg>info@hollowbrookmemorial.org</li>
    <li><svg width="18" height="18" viewBox="0 0 24 24"><circle cx="12" cy="12" r="9" fill="none" stroke="var(--maroon)" stroke-width="2"/><path d="M3 12h18M12 3c3 3 3 15 0 18M12 3c-3 3-3 15 0 18" fill="none" stroke="var(--maroon)" stroke-width="1.6"/></svg>www.hollowbrookmemorial.org</li>
  </ul>

  <figure class="proof before"><span class="tag">Before Care</span><div class="shot" role="img" aria-label="Photo of an untended grave plot with overgrown shrubs before care"></div></figure>
  <figure class="proof after"><span class="tag">After care</span><div class="shot" role="img" aria-label="Photo of a grave plot with trimmed boxwood shrubs after care"></div></figure>
</main>
</body>
</html>
```